Business Cards for new orthopaedic surgery practice

My husband and I are starting our own orthopaedic surgery practice. We are looking for a business card that is uniform, but one will have my name/title and the other will have his. You can just create one design with my name on it for now. But when I choose your design as the winning design I will ask that you add another copy with his name/title.

We are looking for classy, simple, elite all in one. We like dark blues/a little gold/yellow. Something that goes with our logo. We want our logo incorporated. Here is all the info you need:
Business name: RV Bone & Vitality Center
Location: 38517 North Willowmere Ave
Maple Harbor, FL 33490
Phone: 954-218-4063
Fax: 954-582-7341
Email: info@myrvbonecare.example

Names: Lydia Vance, M.D.
Board Certified Hand and Upper Extremity Surgeon

Ebo Dansu, M.D.
Board Certified Hip & Knee Replacement/General Orthopaedic Surgeon

Can decide what you want to put on the back. Maybe a slogan:
Grounded in Skill. Centered on You

I am just going to upload our logo. The only thing is if we select you as the winning design, the location, and phone numbers may change. We will need your help to update that once fully solidified.

Industry/Entity Type

Medical

Contact Information for Business Card

Colors
0054AA
0677BA
7BADD7
CADEEF
E8F1F8
0094D4
00A9DD
6FCCEA
C7EBF8
E9F6FB

Requirements
Must have
• class, appeal,
Should not have
• We want to air on the side of masculine if we are looking at masculine vs. feminine feel. But we still want it classy, sophisticated, and something we will love

```html
<!DOCTYPE html>
<html lang="en">
<head>
<meta charset="utf-8">
<title>RV Bone &amp; Vitality Center – Business Card</title>
<link href="https://fonts.googleapis.com/css2?family=Montserrat:wght@400;500;600&display=swap" rel="stylesheet">
<style>
  :root {
    --backdrop: #1b1b1d;
    --navy: #1c2b57;
    --navy-deep: #17244b;
    --gold: #c9a25f;
    --paper: #ffffff;
    --ink: #1c2b57;
    --mist: #c3c8d2;
  }
  * { margin: 0; padding: 0; box-sizing: border-box; }
  html, body { width: 1200px; height: 897px; overflow: hidden; background: var(--backdrop); }
  body { position: relative; font-family: "Montserrat", sans-serif; }

  .card {
    position: absolute;
    left: 303px;
    width: 594px;
    height: 338px;
    overflow: hidden;
  }
  .card--front { top: 92px; background: var(--paper); }
  .card--back { top: 469px; background: var(--navy); }

  .front-band {
    position: absolute; left: 0; top: 34px; width: 594px; height: 100px;
    background: linear-gradient(90deg, var(--navy) 0%, #22346a 70%, var(--navy) 100%);
  }
  .front-band__accent {
    position: absolute; right: 0; top: 0; width: 61px; height: 100%;
    background: var(--gold);
  }
  .person { position: absolute; left: 33px; top: 23px; color: #fff; }
  .person__name {
    font-weight: 600; font-size: 23px; letter-spacing: 0.6px; color: var(--gold);
    line-height: 1;
  }
  .person__title { font-size: 14px; line-height: 17px; margin-top: 3px; font-weight: 400; }

  .band-mark {
    position: absolute; left: 451px; top: -6px; width: 112px; height: 112px;
    border-radius: 50%; background: #fff;
    display: flex; align-items: center; justify-content: center; text-align: center;
    color: var(--navy); font-weight: 600; font-size: 11px; line-height: 14px; padding: 14px;
  }

  .contact { position: absolute; left: 33px; top: 168px; color: var(--ink); font-size: 14px; }
  .contact__row { display: flex; align-items: center; height: 17px; }
  .contact__row svg { width: 11px; height: 11px; margin-right: 6px; flex: none; }
  .contact__web-accent { color: var(--gold); }
  .address { position: absolute; left: 33px; top: 245px; font-size: 14px; line-height: 18px; color: var(--ink); }
  .slogan { position: absolute; left: 33px; top: 290px; font-size: 14px; font-weight: 500; color: var(--gold); }

  .front-watermark {
    position: absolute; right: 14px; top: 192px; text-align: right;
    color: var(--mist); font-weight: 600; font-size: 30px; line-height: 34px;
  }

  .back-emblem {
    position: absolute; left: 165px; top: 37px; width: 264px; height: 264px;
    border-radius: 50%; border: 2px solid var(--gold);
    display: flex; align-items: center; justify-content: center; text-align: center;
    color: #fff; font-weight: 500; font-size: 22px; line-height: 30px; padding: 30px;
    letter-spacing: 1px;
  }
</style>
</head>
<body>

<section class="card card--front">
  <div class="front-band">
    <div class="front-band__accent"></div>
    <div class="person">
      <h1 class="person__name">LYDIA VANCE, M.D</h1>
      <p class="person__title">Board Certified Hand and<br>Upper Extremity Surgeon</p>
    </div>
    <div class="band-mark">RV Bone &amp; Vitality Center</div>
  </div>

  <div class="contact">
    <div class="contact__row">
      <svg viewBox="0 0 12 12"><path d="M2.5 1 L4.5 1 L5.3 3.4 L4 4.4 Q5 6.8 7.6 8 L8.6 6.7 L11 7.5 L11 9.5 Q10.5 11 9 11 Q1 10 1 2.5 Q1 1 2.5 1Z" fill="#c9a25f"/></svg>
      <span>954-218-4063</span>
    </div>
    <div class="contact__row">
      <svg viewBox="0 0 12 12" fill="none" stroke="#c9a25f" stroke-width="1"><rect x="3" y="1" width="6" height="3"/><rect x="1" y="4" width="10" height="5" rx="1"/><rect x="3" y="7.5" width="6" height="3.5"/></svg>
      <span>954-582-7341</span>
    </div>
    <div class="contact__row">
      <svg viewBox="0 0 12 12" fill="none" stroke="#c9a25f" stroke-width="1"><rect x="1" y="2.5" width="10" height="7"/><path d="M1 2.5 L6 6.5 L11 2.5"/></svg>
      <span>info@myrvbonecare.example</span>
    </div>
    <div class="contact__row">
      <svg viewBox="0 0 12 12" fill="none" stroke="#c9a25f" stroke-width="0.9"><circle cx="6" cy="6" r="5"/><ellipse cx="6" cy="6" rx="2.2" ry="5"/><path d="M1 6 H11 M2 3.5 H10 M2 8.5 H10"/></svg>
      <span>www.<span class="contact__web-accent">myrvbonecare</span>.example</span>
    </div>
  </div>

  <p class="address">38517 North Willowmere Ave<br>Maple Harbor, FL 33490</p>
  <p class="slogan">Grounded in Skill. Centered on You</p>

  <div class="front-watermark">RV Bone &amp;<br>Vitality<br>Center</div>
</section>

<section class="card card--back">
  <div class="back-emblem">RV Bone &amp; Vitality Center</div>
</section>

</body>
</html>
```